Buch-/E-Book-Cover für Referenzbuch der Industrie
Zielgruppe
Als Manufaktur einzigartiger Fachmedien präsentiert verlag-technova Schlüsseltechnologien und ihre Märkte. Faszination für Technik ist die Grundlage unserer Arbeit. Mehr als 30 Jahre verlegerische Erfahrung und das Verständnis für Technologiemärkte machen uns zu einem anerkannten Partner der Industrie.
Unsere Medienmarken knüpfen ein starkes und weit verzweigtes Netzwerk – Print und digital – , in dem sich Anbieter und Anwender von Technologien und Produkten in ihren Zielsetzungen wiederfinden.
Unsere Magazine, Events und Netzwerkveranstaltungen sowie kundenspezifische Kommunikations- & Strategiekampagnen setzen in ihren Zielmärkten Maßstäbe und genießen bei Lesern, Kunden und Partnern Vertrauen und Respekt.
Für das ausgeschriebene Projekt handelt es sich um unsere Referenzpublikation MACHINA.ahead LUMEVETA.
LUMEVETA {polynesisch: Freiraum}
Das Referenzbuch der Industrie. Für Vorwärtsdenker und Zukunftsmacher.
Wandel bestimmt unsere Zeit und verändert unsere Gesellschaft, unsere Unternehmen, uns alle.
Im Wandel liegt Freiraum zur Gestaltung. Gesellschaftlicher Wandel, Technologie-Wandel, Klimawandel, Wertewandel, Führungswandel oder Organisationswandel sind nur einige Beispiele. Wer dabei den Wandel in engen Bahnen denkt, verschenkt Potential. Veränderung braucht Freiraum für neue Ideen und Perspektiven sowie Persönlichkeiten, die diesen nutzen wollen.
Aber wer gestaltet die Zukunft der Industrie und ihrer Branchen? Und wie?
Wir geben Personen aus der Industrie den Freiraum, ihre Perspektiven auf und aus dem Wandel zu erzählen. Warum? Weil sie uns begeistert haben, in persönlichen Treffen und Gesprächen, durch streitbare Meinungen und ehrliche Geschichten. Weil sie die Zukunft verändern.
LUMEVETA ist eine Aufforderung: Zum Mitdenken, Weiterdenken, aber auch Nachdenken.
LUMEVETA – RAUM FÜR NEUES
Ein Referenzbuch, d..
Aufgabenstellung
1. Kurzzusammenfassung der Ausschreibung
Die 4. Ausgabe des jährlichen Referenzbuchs der Industrie, MACHINA.ahead LUMEVETA 2025, erscheint im Oktober 2024. Für das Cover sucht der verlag-technova Verlag neue Vorschläge, die die Themen Freiraum und Wandel in den Fokus stellen.
2. Gestalterische & Inhaltliche Anforderungen
• Format: 195x250 mm + Anschnitt
• Rücken: ca. 1,6 cm (Stand letzte Publikation 2023)
• Auflösung: Druckqualität, mind. 300 dpi
• Inhaltliche Elemente:
- LUMEVETA Schriftzug
- {polynesisch: Freiraum}
- Untersatz: Das Referenzbuch der Industrie. Für Vorwärtsdenker und Zukunftsmacher.
- part of MACHINA.ahead Logo-Balken am unteren Rand (siehe Beispiel AuD_Titelbeispiel_Logobalken)
WICHTIG: Der aktuelle Schriftzug LUMEVETA und die Farbe Orange (0/80/100/0) (siehe Beispiel LUMEVETA 2021) sollen als Wiedererkennung in die Gestaltungen eingebunden werden.

```html
<!DOCTYPE html>
<html lang="de">
<head>
<meta charset="utf-8">
<title>LUMEVETA 2024 – Cover</title>
<link rel="stylesheet" href="https://fonts.googleapis.com/css2?family=Bebas+Neue&family=Oswald:wght@300;400;500;600&display=swap">
<style>
  :root {
    --orange: #e8500f;
    --white: #ffffff;
    --ink: #111111;
    --backdrop: #4a4a4a;
  }
  * { box-sizing: border-box; margin: 0; padding: 0; }
  html, body {
    width: 1200px; height: 1200px; overflow: hidden;
    background: var(--backdrop);
  }
  .cover {
    position: absolute;
    left: 171px; top: 50px;
    width: 858px; height: 1100px;
    background: var(--white);
    overflow: hidden;
  }
  .wordmark {
    position: absolute; left: 0; top: 0;
    width: 270px; height: 1017px;
  }
  .wordmark text {
    font-family: "Bebas Neue", "Oswald", sans-serif;
    font-size: 334px;
    fill: var(--orange);
  }
  .translation {
    position: absolute;
    left: 64px; top: 496px;
    font-family: "Oswald", sans-serif;
    font-weight: 600;
    font-size: 12px;
    color: var(--ink);
    white-space: nowrap;
  }
  .artwork {
    position: absolute;
    left: 292px; top: 60px;
    width: 533px; height: 944px;
    border-radius: 6px;
    background: linear-gradient(160deg,
      rgba(230, 40, 40, .28) 0%,
      rgba(200, 100, 220, .25) 28%,
      rgba(120, 80, 210, .25) 45%,
      rgba(20, 130, 230, .25) 62%,
      rgba(20, 210, 220, .25) 76%,
      rgba(240, 160, 30, .28) 100%);
  }
  .edition {
    position: absolute;
    right: 55px; top: 650px;
    text-align: right;
  }
  .edition-year {
    font-family: "Oswald", sans-serif;
    font-weight: 500;
    font-size: 82px;
    line-height: 1;
    color: var(--orange);
    letter-spacing: -1px;
  }
  .edition-claim {
    margin-top: 18px;
    font-family: "Oswald", sans-serif;
    font-weight: 300;
    font-size: 28px;
    line-height: 39px;
    color: var(--ink);
  }
  .brand-bar {
    position: absolute;
    left: 0; bottom: 0;
    width: 100%; height: 83px;
    background: var(--orange);
    display: flex; align-items: center; justify-content: center;
    gap: 10px;
    color: var(--white);
    font-family: "Oswald", sans-serif;
  }
  .brand-bar-prefix { font-size: 17px; font-weight: 400; }
  .brand-bar-name { font-size: 30px; font-weight: 400; letter-spacing: .5px; }
</style>
</head>
<body>
  <main class="cover">
    <svg class="wordmark" viewBox="0 0 270 1017" aria-label="LUMEVETA">
      <text x="0" y="234" textLength="270" lengthAdjust="spacingAndGlyphs">LU</text>
      <text x="0" y="484" textLength="270" lengthAdjust="spacingAndGlyphs">ME</text>
      <text x="0" y="767" textLength="270" lengthAdjust="spacingAndGlyphs">VE</text>
      <text x="0" y="1017" textLength="270" lengthAdjust="spacingAndGlyphs">TA</text>
    </svg>
    <p class="translation">{polynesisch – Freiraum}</p>

    <div class="artwork" role="img" aria-label="Foto: Papierfalt-Figuren in Regenbogenfarben, aufsteigend von einer zerknüllten Papierkugel über Boot und Schwan zu einem fliegenden Vogel"></div>

    <section class="edition">
      <p class="edition-year">2024</p>
      <p class="edition-claim">Das Referenzbuch<br>der Industrie.<br>Für Vorwärtsdenker<br>und Zukunftsmacher.</p>
    </section>

    <footer class="brand-bar">
      <span class="brand-bar-prefix">part of</span>
      <span class="brand-bar-name">MACHINA.ahead</span>
    </footer>
  </main>
</body>
</html>
```